Business Cards + Flyer + Letterhead for Care Recruitment Agency

We are a recruitment agency for the health & care sector. We need designs made for business cards, A5 double-sided flyer, and a letterhead template.

Our branding message is professionalism, care, compassion, expertise. We are experts in recruitment for the care & health industry.

Our logo source files and colours are here - https://www.filevault-example.net/sh/q8rn27lpzw4xkc/BBRtLm3QPW92dKfYhNvZceLmo?dl=0

For the business card, I have attached an example we like. We want a vertical business card design, something very similar to the example given. The design should match our logo in terms of brand colors. On one side should be our logo, our website (www.holbrookelune.co.uk) and Care Recruitment Specialists written somewhere visible that fits, between our logo and the website at the bottom. On the other side should be our details.

Details on the front:

Logo with slogan
Care Recruitment Specialists
www.holbrookelune.co.uk

Details on the back:

Dominic Argyros
Managing Director

Radley Court, 40-48 Pellow St, Birmingham, B7 9QX
07612 495137
dominic@holbrookelune.co.uk
www.holbrookelune.co.uk

Nadia Holbrooke
Business Development Director

07731 284956
nadia@holbrookelune.co.uk
www.holbrookelune.co.uk

For the A5 flyer, I have attached some pictures we've used for the website, which could be used for the flyer as well. To get a better idea of our branding, please visit our website - https://holbrookelune.co.uk/

The text for the flyer is also attached.

Finally, the letterhead template should be a docx template with our logo and our identifiable branding (the same shapes and matching colours you will come up with for the business cards and flyer).

```html
<!DOCTYPE html>
<html lang="en">
<head>
<meta charset="utf-8">
<title>Holbrooke Lune – Letterhead</title>
<link rel="stylesheet" href="https://fonts.googleapis.com/css2?family=Montserrat:wght@700&family=Roboto+Condensed:wght@700&family=Arimo:wght@400&display=swap">
<style>
  :root {
    --navy: #233f8a;
    --navy-deep: #1c2a5a;
    --sky: #aed6f1;
    --band-top: #1f4290;
    --band-bottom: #1b1f3f;
    --cyan: #3ec8f0;
    --brand-light: #3b8fd4;
    --paper: #ffffff;
  }
  html, body {
    margin: 0;
    padding: 0;
    width: 848px;
    height: 1200px;
    overflow: hidden;
    background: var(--paper);
  }
  .letterhead {
    position: relative;
    width: 848px;
    height: 1200px;
    background: var(--paper);
  }
  .brand {
    position: absolute;
    left: 41px;
    top: 48px;
    width: 175px;
    text-align: center;
  }
  .brand-dot {
    display: block;
    width: 44px;
    height: 44px;
    margin: 0 auto 14px;
    border-radius: 50%;
    background: var(--brand-light);
  }
  .brand-name {
    display: block;
    font-family: "Montserrat", sans-serif;
    font-weight: 700;
    font-size: 16px;
    letter-spacing: 1.6px;
    color: var(--navy-deep);
    white-space: nowrap;
  }
  .header-info {
    position: absolute;
    left: 307px;
    top: 51px;
  }
  .header-title {
    margin: 0 0 2px;
    font-family: "Roboto Condensed", sans-serif;
    font-weight: 700;
    font-size: 24px;
    line-height: 26px;
    letter-spacing: 0.9px;
    color: var(--navy);
  }
  .header-address {
    margin: 0;
    font-family: "Arimo", sans-serif;
    font-style: normal;
    font-size: 17px;
    line-height: 21px;
    letter-spacing: 0.6px;
    color: var(--navy);
  }
  .header-rule {
    position: absolute;
    left: 307px;
    right: 0;
    top: 125px;
    height: 2px;
    background: var(--navy);
  }
  .footer-band {
    position: absolute;
    left: 0;
    bottom: 0;
    width: 848px;
    height: 170px;
    display: block;
  }
  .footer-contacts {
    position: absolute;
    left: 40px;
    top: 1086px;
    margin: 0;
    padding: 0;
    list-style: none;
  }
  .contact-item {
    display: flex;
    align-items: center;
    height: 22px;
    margin-bottom: 6px;
    font-family: "Arimo", sans-serif;
    font-size: 16px;
    letter-spacing: 1px;
    color: var(--paper);
  }
  .contact-icon {
    width: 21px;
    height: 21px;
    margin-right: 9px;
    flex: none;
  }
</style>
</head>
<body>
<div class="letterhead">

  <div class="brand">
    <span class="brand-dot"></span>
    <span class="brand-name">HOLBROOKE LUNE</span>
  </div>

  <div class="header-info">
    <h1 class="header-title">CARE RECRUITMENT SPECIALISTS</h1>
    <address class="header-address">Radley Court, 40-48 Pellow St,<br>Birmingham, B7 9QX</address>
  </div>
  <div class="header-rule"></div>

  <svg class="footer-band" viewBox="0 0 848 170" preserveAspectRatio="none" aria-hidden="true">
    <defs>
      <linearGradient id="band-fill" x1="0" y1="0" x2="0" y2="1">
        <stop offset="0" stop-color="var(--band-top)"/>
        <stop offset="1" stop-color="var(--band-bottom)"/>
      </linearGradient>
    </defs>
    <path fill="var(--sky)" d="M0,20 Q424,-10 848,60 L848,170 L0,170 Z"/>
    <path fill="url(#band-fill)" d="M0,34 Q424,8 848,90 L848,170 L0,170 Z"/>
  </svg>

  <ul class="footer-contacts">
    <li class="contact-item">
      <svg class="contact-icon" viewBox="0 0 22 22" aria-hidden="true">
        <circle cx="11" cy="11" r="9.8" fill="none" stroke="var(--cyan)" stroke-width="1.5"/>
        <path fill="var(--cyan)" d="M7.2,6.2 l1.8,-0.6 1.2,2.6 -1.1,0.9 c0.5,1.3 1.4,2.3 2.6,2.9 l1,-1 2.5,1.3 -0.6,1.8 c-3.8,0.2 -7.6,-3.8 -7.4,-7.9z"/>
      </svg>
      07612 495137
    </li>
    <li class="contact-item">
      <svg class="contact-icon" viewBox="0 0 22 22" aria-hidden="true">
        <circle cx="11" cy="11" r="9.8" fill="none" stroke="var(--cyan)" stroke-width="1.5"/>
        <rect x="6" y="7.5" width="10" height="7" fill="var(--cyan)"/>
        <path d="M6,7.5 L11,11.5 L16,7.5" fill="none" stroke="var(--navy-deep)" stroke-width="0.8"/>
      </svg>
      dominic@holbrookelune.co.uk
    </li>
    <li class="contact-item">
      <svg class="contact-icon" viewBox="0 0 22 22" aria-hidden="true">
        <circle cx="11" cy="11" r="9.8" fill="none" stroke="var(--cyan)" stroke-width="1.5"/>
        <path fill="var(--cyan)" d="M8,5.5 L8,15 L10.2,13 L11.8,16.5 L13.2,15.8 L11.6,12.4 L14.4,12.2 Z"/>
      </svg>
      www.holbrookelune.co.uk
    </li>
  </ul>

</div>
</body>
</html>
```